Business Card Design Project

- makeup artist business card

- original and creative

- Elegant design

- Feel free to come out with cool designs but stick to being elegant and attractive

- Design relates to makeup

- includes name, occupation, contact numbers, email, website

- regular size business card

- round corner card

- double sided

- on 1 side it should just have the website name in the center " moonveilstudio.net "

Industry/Entity Type

Business

Requirements
Must have
• Delia Marsh
Makeup Artist
USA: +1 (415)772-0461
Singapore: +65 82307915
deliamarsh@moonveilstudio.net
www.moonveilstudio.net
Should not have
• nothing cartoon looking.
Pictures of makeup being grab from the internet.. Examples: eyes or lips.

```html
<!DOCTYPE html>
<html lang="en">
<head>
<meta charset="utf-8">
<title>Delia Marsh — Makeup Artist Business Card</title>
<link rel="stylesheet" href="https://fonts.googleapis.com/css2?family=Arimo:wght@400;700&display=swap">
<style>
  :root {
    --page-bg: #f2e6ea;
    --plum-light: #a02c72;
    --plum-mid: #8c2467;
    --plum-dark: #74205a;
    --card-white: #ffffff;
    --text-white: #ffffff;
    --text-blush: #f3c6de;
    --text-blush-soft: #e3a2c6;
    --shadow: rgba(60, 20, 45, 0.28);
  }
  * { margin: 0; padding: 0; box-sizing: border-box; }
  html, body {
    width: 1200px;
    height: 951px;
    overflow: hidden;
    background: var(--page-bg);
    font-family: "Arimo", Arial, sans-serif;
  }
  .canvas {
    position: relative;
    width: 1200px;
    height: 951px;
  }
  .card {
    position: absolute;
    left: 250px;
    width: 700px;
    height: 400px;
    border-radius: 28px;
    overflow: hidden;
    box-shadow: 0 14px 30px var(--shadow);
  }
  .plum-surface {
    background: radial-gradient(ellipse at 42% 48%, var(--plum-light) 0%, var(--plum-mid) 45%, var(--plum-dark) 100%);
  }

  /* Back side: website only */
  .card-back {
    top: 50px;
    display: flex;
    align-items: center;
    justify-content: center;
  }
  .web-line {
    display: flex;
    align-items: center;
    gap: 18px;
  }
  .dot-trail {
    display: flex;
    align-items: center;
    gap: 9px;
  }
  .dot-trail span {
    display: block;
    border-radius: 50%;
    background: var(--text-white);
  }
  .dot-trail span:nth-child(1) { width: 4px; height: 4px; opacity: .6; }
  .dot-trail span:nth-child(2) { width: 5px; height: 5px; opacity: .7; }
  .dot-trail span:nth-child(3) { width: 6px; height: 6px; opacity: .8; }
  .dot-trail span:nth-child(4) { width: 7px; height: 7px; opacity: .9; }
  .dot-trail span:nth-child(5) { width: 9px; height: 9px; }
  .web-address {
    font-size: 30px;
    letter-spacing: 3px;
    color: var(--text-blush);
  }
  .web-address .web-affix { color: var(--text-blush-soft); }

  /* Front side: name and contacts */
  .card-front {
    top: 500px;
    background: var(--card-white);
  }
  .front-panel {
    position: absolute;
    left: 14px;
    top: 14px;
    right: 44px;
    bottom: 14px;
    border-radius: 18px 4px 4px 18px;
    overflow: hidden;
  }
  .identity {
    position: absolute;
    left: 38px;
    top: 36px;
    display: flex;
    flex-direction: column;
    align-items: flex-end;
    gap: 8px;
  }
  .person-name {
    font-weight: 700;
    font-size: 40px;
    line-height: 1.1;
    letter-spacing: 1px;
    color: var(--text-white);
    text-transform: uppercase;
  }
  .person-role {
    font-size: 22px;
    color: var(--text-white);
  }
  .contact-list {
    position: absolute;
    right: 28px;
    bottom: 34px;
    list-style: none;
    font-size: 20px;
    line-height: 1.3;
    color: var(--text-white);
    white-space: nowrap;
  }
</style>
</head>
<body>
<main class="canvas">

  <section class="card card-back plum-surface" aria-label="Business card back">
    <div class="web-line">
      <div class="dot-trail" aria-hidden="true"><span></span><span></span><span></span><span></span><span></span></div>
      <p class="web-address"><span class="web-affix">www.</span>moonveilstudio<span class="web-affix">.net</span></p>
    </div>
  </section>

  <section class="card card-front" aria-label="Business card front">
    <div class="front-panel plum-surface">
      <div class="identity">
        <h1 class="person-name">Delia Marsh</h1>
        <p class="person-role">Makeup Artist</p>
      </div>
      <ul class="contact-list">
        <li>USA: +1 (415)772-0461</li>
        <li>Singapore: +65 82307915</li>
        <li>deliamarsh@moonveilstudio.net</li>
      </ul>
    </div>
  </section>

</main>
</body>
</html>
```